Quick Straightforward Billboard Redesign

- Design billboard sized for 10 foot' x 36' foot width live area size and please include bleeds 6" around all sides
- Exact blue color match is imperative in headline, logo, phone number bubble or wherever used. C-83 / M-45 / Y-1 / K-0-
- What I hope to illustrate is that our company offers the best porch screening in the area area, in regards to quality, expertise, durability, storms proof, but we do not build screen porches.
- Current board is attached below from previous designer, and as you can see sizing was off, white space on edges make it appear to be sized incorrectly.
- I also attached my own little mock up idea well well if it helps, favorite image, logo, headline, etc and ideas perhaps on expanding or making this better?

Thanks so much!

Target Market(s)

Drivers and passengers, Southeastern NC, are of immense new construction and high end homes.

Industry/Entity Type

Construction

Colors
0054AA
0677BA
7BADD7
CADEEF
E8F1F8

Requirements
Must have
• Blue color matching
Nice to have
• Design spins or other thoughts on my little mock up

```html
<!DOCTYPE html>
<html lang="en">
<head>
<meta charset="utf-8">
<title>Tidewater Mesh – Billboard</title>
<link rel="stylesheet" href="https://fonts.googleapis.com/css2?family=League+Spartan:wght@700&family=Oswald:wght@700&display=swap">
<style>
  :root {
    --brand-blue: #0868b4;
    --brand-green: #06b45f;
    --sky-blue: #7badd7;
    --paper: #f6f7f8;
    --paper-shade: #e6e8ea;
    --number-white: #f1f1f1;
    --stage: #30343d;
  }
  html, body {
    margin: 0;
    padding: 0;
    width: 1145px;
    height: 1200px;
    overflow: hidden;
    background: var(--stage);
  }
  .billboard {
    position: absolute;
    left: 50px;
    top: 442px;
    width: 1045px;
    height: 315px;
    box-shadow: 0 10px 24px rgba(0, 0, 0, 0.45);
  }
  .billboard svg { display: block; }
  .headline {
    font-family: "League Spartan", "Montserrat", sans-serif;
    font-weight: 700;
    font-size: 86px;
  }
  .headline--blue { fill: var(--brand-blue); }
  .headline--white { fill: #ffffff; }
  .brand-name {
    font-family: "League Spartan", "Montserrat", sans-serif;
    font-weight: 700;
    font-size: 44px;
    fill: var(--brand-blue);
  }
  .phone-number {
    font-family: "Oswald", sans-serif;
    font-weight: 700;
    font-size: 66px;
    fill: var(--number-white);
  }
</style>
</head>
<body>
  <div class="billboard">
    <svg width="1045" height="315" viewBox="0 0 1045 315">
      <defs>
        <linearGradient id="porch-wash" x1="0" y1="0" x2="1" y2="1">
          <stop offset="0" stop-color="var(--paper)"/>
          <stop offset="0.5" stop-color="var(--paper-shade)"/>
          <stop offset="1" stop-color="var(--paper)"/>
        </linearGradient>
        <filter id="pill-shadow" x="-5%" y="-20%" width="110%" height="150%">
          <feDropShadow dx="0" dy="3" stdDeviation="3" flood-color="#000" flood-opacity="0.3"/>
        </filter>
      </defs>

      <rect class="porch-photo" x="0" y="0" width="1045" height="315" fill="url(#porch-wash)" role="img" aria-label="Faint photo of a screened porch with wicker furniture and palm fronds"/>

      <text class="headline headline--blue" x="43" y="92" textLength="960" lengthAdjust="spacingAndGlyphs">SCREEN YOUR PORCH.</text>

      <rect class="tagline-band" x="0" y="117" width="1045" height="77" fill="var(--brand-green)"/>
      <text class="headline headline--white" x="47" y="184" textLength="955" lengthAdjust="spacingAndGlyphs">BUILT FOR THE COAST.</text>

      <g class="brand">
        <rect class="brand-mark" x="47" y="246" width="34" height="34" fill="var(--sky-blue)"/>
        <text class="brand-name" x="97" y="280" textLength="390" lengthAdjust="spacingAndGlyphs">TIDEWATER MESH</text>
      </g>

      <g class="phone-pill">
        <path d="M565 209 H1045 V285 H565 Q553 285 553 273 V221 Q553 209 565 209 Z" fill="var(--brand-blue)" filter="url(#pill-shadow)"/>
        <circle cx="588" cy="247" r="25" fill="#ffffff"/>
        <circle cx="588" cy="247" r="21" fill="var(--brand-green)"/>
        <path class="phone-icon" d="M578 236 q3 -2 5 1 l3 5 q1 3 -1 4 l-2 1 q2 6 8 9 l1 -2 q2 -2 4 -1 l5 3 q3 2 1 5 l-2 2 q-3 3 -8 1 q-13 -5 -17 -19 q-1 -5 3 -9 z" fill="#ffffff"/>
        <path d="M591 236 a9 9 0 0 1 8 8 M591 231 a14 14 0 0 1 13 13" stroke="#ffffff" stroke-width="2" fill="none" stroke-linecap="round"/>
        <text class="phone-number" x="628" y="272" textLength="374" lengthAdjust="spacingAndGlyphs">555.014.2287</text>
      </g>
    </svg>
  </div>
</body>
</html>
```